Flyer for Tallow Brisko - Design Agency

We need a 4-page square flyer measuring 14.8x14.8cm per page, to fold out, for a design agency targeting small businesses.
The design should be very modern. There shouldn't be too much content visible.
The background should be black. The color of the logo (attached) can also be used. The content is also attached and divided per page. We are open to alternative suggestions regarding the division.

```html
<!DOCTYPE html>
<html lang="de">
<head>
<meta charset="utf-8">
<title>Tallow Brisko – Faltflyer</title>
<link rel="stylesheet" href="https://fonts.googleapis.com/css2?family=Questrial&display=swap">
<style>
  :root {
    --backdrop: #d3d3d3;
    --paper: #0b0b0c;
    --brand: #8fd0ea;
    --text: #e6e6e6;
    --muted: #b9b9b9;
    --faint: #2a2a2b;
    --fold: #1a1a1b;
  }
  * { margin: 0; padding: 0; box-sizing: border-box; }
  html, body { width: 1088px; height: 1200px; overflow: hidden; }
  body {
    background: var(--backdrop);
    font-family: "Questrial", sans-serif;
    color: var(--text);
    position: relative;
  }
  .spread {
    position: absolute;
    left: 91px;
    width: 911px;
    height: 455px;
    background: var(--paper);
    display: flex;
  }
  .spread--outside { top: 81px; }
  .spread--inside { top: 663px; }
  .page {
    position: relative;
    width: 50%;
    height: 100%;
    overflow: hidden;
  }
  .page + .page { border-left: 1px solid var(--fold); }
  .center { position: absolute; left: 0; right: 0; text-align: center; }

  .wordmark {
    color: var(--brand);
    font-size: 24px;
    line-height: 22px;
    letter-spacing: 0.5px;
    text-transform: lowercase;
  }
  .wordmark--large { font-size: 36px; line-height: 34px; }

  .contact { font-size: 9px; letter-spacing: 0.2px; color: var(--text); text-transform: uppercase; }
  .contact--lead { color: var(--muted); }
  .owners { font-size: 9px; color: var(--muted); text-transform: uppercase; }
  .tagline { font-size: 9.5px; color: var(--muted); text-transform: uppercase; }

  .backdrop-name {
    position: absolute;
    left: 38px;
    top: 52px;
    color: var(--faint);
    font-size: 122px;
    line-height: 100px;
    letter-spacing: -2px;
    text-transform: lowercase;
    white-space: nowrap;
  }

  .photo { position: absolute; }
  .photo--open-laptop {
    left: 84px; top: 118px; width: 272px; height: 194px;
    background:
      radial-gradient(ellipse 50% 28% at 52% 42%, rgba(255,122,78,.95) 0%, rgba(226,69,58,.8) 45%, transparent 80%),
      radial-gradient(ellipse 30% 35% at 42% 82%, rgba(40,150,170,.55) 0%, transparent 75%),
      radial-gradient(ellipse 22% 40% at 60% 85%, rgba(200,30,40,.55) 0%, transparent 75%);
  }
  .photo--closed-laptop {
    left: 75px; top: 158px; width: 298px; height: 132px;
    background:
      radial-gradient(ellipse 35% 30% at 30% 45%, rgba(200,50,80,.75) 0%, transparent 75%),
      radial-gradient(ellipse 35% 30% at 65% 70%, rgba(70,150,220,.75) 0%, transparent 75%);
  }

  .headline { font-size: 16.5px; line-height: 19px; color: var(--text); }
  .intro { font-size: 9.5px; line-height: 12px; color: var(--text); }

  .section-title {
    position: absolute;
    font-size: 13.5px;
    font-weight: 400;
    text-transform: uppercase;
    color: var(--text);
  }
  .service { position: absolute; width: 185px; }
  .service__number {
    position: absolute; left: -17px; top: 2px;
    font-size: 19px; color: var(--text);
  }
  .service__title { font-size: 9.5px; line-height: 12px; color: var(--text); }
  .service__text { font-size: 9.5px; line-height: 12px; color: var(--brand); }

  .reason { position: absolute; width: 185px; }
  .reason__icon { position: absolute; left: -30px; top: 0; width: 24px; height: 24px; }
  .reason__title { font-size: 9.5px; line-height: 13px; color: var(--text); }
  .reason__text { font-size: 10.5px; line-height: 13px; color: var(--brand); }

  .closing { font-size: 9.5px; letter-spacing: 1.3px; color: var(--text); }
</style>
</head>
<body>

<section class="spread spread--outside">
  <div class="page page--back">
    <div class="center wordmark" style="top:177px;">tallow<br>brisko</div>
    <p class="center contact contact--lead" style="top:237px;">Kontaktiere uns für eine kostenlose Beratung!</p>
    <p class="center contact" style="top:258px;">+49 069 28 4410 &nbsp;|&nbsp; hallo@tallowbrisko.de</p>
    <p class="center contact" style="top:277px;">Lindenhofweg 42, 60311 Frankfurt</p>
    <p class="center owners" style="top:402px;">Inhaber : Jona Wirth &amp; Ilka Marten</p>
  </div>
  <div class="page page--cover">
    <div class="backdrop-name" aria-hidden="true">tallow<br>brisko</div>
    <div class="photo photo--open-laptop" role="img" aria-label="Aufgeklappter Laptop mit farbig leuchtender Tastatur in Rot und Orange vor schwarzem Grund"></div>
    <div class="center wordmark wordmark--large" style="top:302px;">tallow<br>brisko</div>
    <p class="center tagline" style="top:405px;">Designs, die wirken. Marken, die bleiben.</p>
  </div>
</section>

<section class="spread spread--inside">
  <div class="page page--intro">
    <div class="center wordmark" style="top:53px;">tallow<br>brisko</div>
    <div class="photo photo--closed-laptop" role="img" aria-label="Fast geschlossener Laptop im Dunkeln mit rotem und blauem Lichtschein"></div>
    <p class="center headline" style="top:330px;">Tallow Brisko gestaltet die Zukunft deines<br>Unternehmensauftritts.</p>
    <p class="center intro" style="top:382px;">Wir machen aus Ideen visuelle Erlebnisse und sorgen dafür,<br>dass deine Marke im Gedächtnis bleibt.</p>
  </div>
  <div class="page page--services">
    <h2 class="section-title" style="left:17px; top:44px;">Unsere Leistungen:</h2>

    <div class="service" style="left:43px; top:92px;">
      <span class="service__number">1</span>
      <p class="service__title">Next-Level Flyer</p>
      <p class="service__text">Nicht nur Papier, sondern deine<br>Botschaft im perfekten Look.</p>
    </div>
    <div class="service" style="left:263px; top:92px;">
      <span class="service__number">2</span>
      <p class="service__title">Corporate Identity</p>
      <p class="service__text">Ein Design, das deine Marke<br>spricht – individuell, stark,<br>unvergesslich.</p>
    </div>
    <div class="service" style="left:43px; top:174px;">
      <span class="service__number">3</span>
      <p class="service__title">Digital &amp; Print</p>
      <p class="service__text">Ob Social Media Grafiken oder<br>klassisches Printdesign – wir sind da,<br>wo du uns brauchst.</p>
    </div>
    <div class="service" style="left:263px; top:174px;">
      <span class="service__number">4</span>
      <p class="service__title">Alles aus einer Hand</p>
      <p class="service__text">Logo, Farben, Typografie, Flyer<br>und vieles mehr – wir bauen das<br>Fundament für deinen Erfolg.</p>
    </div>

    <h2 class="section-title" style="left:23px; top:280px;">Warum wir?</h2>

    <div class="reason" style="left:53px; top:329px;">
      <svg class="reason__icon" viewBox="0 0 24 24" aria-hidden="true">
        <path d="M20 9 A10 10 0 1 1 15 3.5" fill="none" stroke="var(--brand)" stroke-width="1.3"/>
        <path d="M7 12 L11 16 L21 4" fill="none" stroke="var(--brand)" stroke-width="1.3"/>
      </svg>
      <p class="reason__title">Dein Style, unser Know-how</p>
      <p class="reason__text">Wir kombinieren deine Vision mit<br>moderner Ästhetik.</p>
    </div>
    <div class="reason" style="left:275px; top:329px;">
      <svg class="reason__icon" viewBox="0 0 24 24" aria-hidden="true">
        <path d="M20 9 A10 10 0 1 1 15 3.5" fill="none" stroke="var(--brand)" stroke-width="1.3"/>
        <path d="M7 12 L11 16 L21 4" fill="none" stroke="var(--brand)" stroke-width="1.3"/>
      </svg>
      <p class="reason__title">Persönlicher Service</p>
      <p class="reason__text">Wir hören zu und setzen um,<br>was dich einzigartig macht</p>
    </div>

    <p class="center closing" style="top:405px; left:24px;">Flexible Lösungen für die unterschiedlichsten Anforderungen</p>
  </div>
</section>

</body>
</html>
```